Maple Roster Business Card for recruitment company

We are looking for a Business Card Design that incorporates our personal details and our busines name and logo. We are a specialized search consultancy that recruit Property and Construction professionals.
We would like a business card that stands out and is appealing to the Construction and Property industry as well.

Target Market(s)

people in the construction and property industry

Contact Information for Business Card

Business Name and logo

Font styles to use
Serif

Colors
0094D4
00A9DD
6FCCEA
C7EBF8
E9F6FB

Requirements
Must have
• Business name and logo as well as contact details
Should not have
• No photos of us please

```html
<!DOCTYPE html>
<html lang="en">
<head>
<meta charset="utf-8">
<title>Maple Roster – Business Card</title>
<link href="https://fonts.googleapis.com/css2?family=Open+Sans:ital,wght@0,300;0,400;0,700;1,400&display=swap" rel="stylesheet">
<style>
  :root {
    --bg: #1c1e20;
    --teal: #005f73;
    --teal-deep: #004656;
    --teal-light: #0a7288;
    --paper: #f1f2f3;
    --paper-shade: #e2e4e6;
    --silver: #a7a9ac;
    --white: #ffffff;
  }
  * { margin: 0; padding: 0; box-sizing: border-box; }
  html, body {
    width: 1200px; height: 900px; overflow: hidden;
    background: var(--bg);
    font-family: "Open Sans", Arial, sans-serif;
  }
  .sheet {
    width: 1200px; height: 900px;
    display: flex; flex-direction: column;
    align-items: center; justify-content: center; gap: 60px;
  }
  .card {
    position: relative;
    width: 580px; height: 330px;
    border-radius: 22px;
    overflow: hidden;
    box-shadow: 0 14px 30px rgba(0,0,0,0.55);
  }
  /* front */
  .card--front {
    background: linear-gradient(160deg, var(--white) 0%, var(--paper) 60%, var(--paper-shade) 100%);
  }
  .card__wave { position: absolute; inset: 0; width: 100%; height: 100%; }
  .wordmark {
    font-weight: 300;
    letter-spacing: 0.06em;
    text-transform: uppercase;
    white-space: nowrap;
  }
  .card--front .wordmark {
    position: absolute; right: 46px; top: 96px;
    font-size: 38px; color: var(--teal);
  }
  .contact {
    position: absolute; left: 34px; bottom: 40px;
    color: var(--white);
  }
  .contact__name { font-weight: 700; font-size: 15px; line-height: 1.3; }
  .contact__role { font-size: 12px; line-height: 1.35; font-weight: 400; }
  .contact__list { list-style: none; margin-top: 12px; }
  .contact__item {
    display: flex; align-items: center; gap: 8px;
    font-size: 12px; line-height: 1.55;
  }
  .contact__icon { width: 11px; height: 11px; flex: none; }
  /* back */
  .card--back {
    background: radial-gradient(ellipse at 40% 85%, var(--teal-light) 0%, var(--teal) 45%, var(--teal-deep) 100%);
    display: flex; flex-direction: column;
    align-items: center; justify-content: center; gap: 34px;
  }
  .card--back .wordmark { font-size: 48px; color: var(--paper); }
  .card--back .web {
    font-size: 12px; letter-spacing: 0.32em; color: var(--paper);
  }
</style>
</head>
<body>
<main class="sheet">

  <section class="card card--front" aria-label="Business card front">
    <svg class="card__wave" viewBox="0 0 580 330" preserveAspectRatio="none" aria-hidden="true">
      <defs>
        <linearGradient id="tealFill" x1="0" y1="0" x2="1" y2="1">
          <stop offset="0" stop-color="#004e60"/>
          <stop offset="0.6" stop-color="#006579"/>
          <stop offset="1" stop-color="#005466"/>
        </linearGradient>
      </defs>
      <path d="M0,78 C140,82 250,120 300,215 C335,285 390,318 540,330 L0,330 Z" fill="#a7a9ac"/>
      <path d="M0,90 C140,94 245,132 294,222 C330,290 385,322 530,338 L0,338 Z" fill="#ffffff"/>
      <path d="M0,94 C140,98 242,136 290,226 C326,294 380,326 520,342 L0,342 Z" fill="url(#tealFill)"/>
    </svg>

    <div class="wordmark">Maple Roster</div>

    <div class="contact">
      <p class="contact__name">Clara Bennett</p>
      <p class="contact__role">Director</p>
      <p class="contact__role">Senior Search Consultant</p>
      <ul class="contact__list">
        <li class="contact__item">
          <svg class="contact__icon" viewBox="0 0 12 12" aria-hidden="true"><path d="M2.5 1 L4.5 1 L5.3 3.6 L4 4.6 C4.6 6 5.9 7.4 7.4 8 L8.4 6.7 L11 7.5 L11 9.5 C11 10.4 10.3 11 9.4 11 C5 10.6 1.4 7 1 2.6 C1 1.7 1.6 1 2.5 1 Z" fill="#ffffff"/></svg>
          <span>+64 21 480 2957</span>
        </li>
        <li class="contact__item">
          <svg class="contact__icon" viewBox="0 0 12 12" aria-hidden="true"><rect x="0.5" y="2.5" width="11" height="7" fill="#ffffff"/><path d="M0.5 2.5 L6 6.8 L11.5 2.5" fill="none" stroke="#005f73" stroke-width="1"/></svg>
          <span>clara@mapleroster.nz</span>
        </li>
        <li class="contact__item">
          <svg class="contact__icon" viewBox="0 0 12 12" aria-hidden="true"><circle cx="6" cy="6" r="5" fill="none" stroke="#ffffff" stroke-width="1.1"/><ellipse cx="6" cy="6" rx="2.2" ry="5" fill="none" stroke="#ffffff" stroke-width="1"/><path d="M1 6 H11 M2 3.5 H10 M2 8.5 H10" stroke="#ffffff" stroke-width="0.9"/></svg>
          <span>www.mapleroster.nz</span>
        </li>
      </ul>
    </div>
  </section>

  <section class="card card--back" aria-label="Business card back">
    <div class="wordmark">Maple Roster</div>
    <p class="web">www.mapleroster.nz</p>
  </section>

</main>
</body>
</html>
```